Thornbury Building Company - Card Design

I am looking to use the logo designs that you already did for me to develop a business card. I would like the card to have a black background and be double sided. I want white and green logo and text. I have attached an inspiration photo of a look that I like. I would like to use the Vertical Logo attached to take up the full front side of the card. On the back where I have my name and information, I would like to have the horizontal logo or maybe even just the image of the 'A' and trees without the text. I am open, but I am looking for something clean and simple and I want the green to really pop! Additional files can be found under Design #: 58302946

Target Market(s)

Homeowners

Industry/Entity Type

Construction

Contact Information for Business Card

Name: Marcus Thornbury, Title: Project Manager, Phone: 555.274.8136, Email: thornburybuildingcompany@mailvesta.com, address: 487 Larkspur Ln, Alderbrook, CA 95033, Lic# 2468317

Colors
00AB8E
00BBA5
67D7C9
C6EFE9
E9F9F6

Requirements
Nice to have
• I would like to see the logos that I have already got from ArtLoomHub, though I am open to new ones

```html
<!DOCTYPE html>
<html lang="en">
<head>
<meta charset="utf-8">
<title>Thornbury Building Company – Business Card</title>
<link rel="stylesheet" href="https://fonts.googleapis.com/css2?family=Arimo:wght@400;700&display=swap">
<style>
  :root {
    --page-bg: #d6d6d4;
    --card-black: #1c1c1c;
    --card-deep: #141414;
    --brand-green: #5fbb46;
    --text-white: #ffffff;
    --mark-grey: #2c2c2c;
  }
  * { box-sizing: border-box; margin: 0; padding: 0; }
  html, body {
    width: 1200px; height: 801px; overflow: hidden;
    background: var(--page-bg);
    font-family: "Arimo", Arial, sans-serif;
  }
  .sheet {
    position: relative; width: 1200px; height: 801px;
    display: flex; align-items: center; justify-content: center; gap: 24px;
  }
  .card {
    position: relative; width: 556px; height: 318px;
    background: var(--card-black);
    border-bottom: 4px solid var(--brand-green);
    border-right: 2px solid var(--brand-green);
    overflow: hidden;
  }
  /* Front: contact side */
  .card-front__mark-area {
    position: absolute; right: 0; top: 0; width: 230px; height: 100%;
    background: radial-gradient(ellipse at 60% 40%, #232a22 0%, var(--card-black) 70%);
  }
  .brand {
    display: flex; align-items: center; gap: 10px;
    color: var(--text-white); font-weight: 700; text-transform: uppercase;
  }
  .brand__square { width: 22px; height: 22px; background: var(--brand-green); }
  .card-front .brand { position: absolute; left: 44px; top: 58px; font-size: 19px; letter-spacing: 1px; }
  .contact { position: absolute; left: 44px; top: 122px; color: var(--text-white); }
  .contact__accent {
    position: absolute; left: -44px; top: 54px; width: 14px; height: 36px;
    background: var(--brand-green);
  }
  .contact__name {
    font-size: 22px; font-weight: 700; color: var(--brand-green);
    text-transform: uppercase; letter-spacing: 0.5px;
  }
  .contact__title { font-size: 14px; margin-top: 3px; }
  .contact__licence { font-size: 13px; color: var(--brand-green); margin-top: 18px; }
  .contact__address { font-size: 13px; margin-top: 3px; }
  .contact__line { display: flex; align-items: center; gap: 8px; font-size: 13px; margin-top: 8px; }
  .contact__line:first-of-type { margin-top: 14px; }
  .contact__icon { width: 12px; height: 12px; flex: none; }
  /* Back: brand side */
  .card-back__pattern {
    position: absolute; inset: 0;
    background: linear-gradient(160deg, #3a3a3a 0%, #262626 40%, var(--card-deep) 100%);
  }
  .card-back .brand { position: absolute; right: 28px; bottom: 46px; font-size: 18px; letter-spacing: 1px; }
</style>
</head>
<body>
<main class="sheet">
  <section class="card card-front" aria-label="Business card front">
    <div class="card-front__mark-area" role="img" aria-label="Large faint company mark in dark green and grey"></div>
    <div class="brand"><span class="brand__square"></span><span>Thornbury Building Company</span></div>
    <div class="contact">
      <span class="contact__accent"></span>
      <p class="contact__name">Marcus Thornbury</p>
      <p class="contact__title">Project Manager</p>
      <p class="contact__licence">Lic# 2468317</p>
      <p class="contact__address">487 Larkspur Ln, Alderbrook, CA 95033</p>
      <p class="contact__line">
        <svg class="contact__icon" viewBox="0 0 24 24"><path fill="#5fbb46" d="M6.6 10.8a15 15 0 0 0 6.6 6.6l2.2-2.2a1 1 0 0 1 1-.25 11.4 11.4 0 0 0 3.6.6 1 1 0 0 1 1 1V20a1 1 0 0 1-1 1A17 17 0 0 1 3 4a1 1 0 0 1 1-1h3.5a1 1 0 0 1 1 1c0 1.25.2 2.45.6 3.6a1 1 0 0 1-.25 1z"/></svg>
        <span>555.274.8136</span>
      </p>
      <p class="contact__line">
        <svg class="contact__icon" viewBox="0 0 24 24"><path fill="#5fbb46" d="M2 5h20v14H2z"/><path fill="none" stroke="#1c1c1c" stroke-width="2" d="M2 5l10 8 10-8"/></svg>
        <span>thornburybuildingcompany@mailvesta.com</span>
      </p>
    </div>
  </section>

  <section class="card card-back" aria-label="Business card back">
    <div class="card-back__pattern" role="img" aria-label="Repeating pattern of the company mark in shades of grey"></div>
    <div class="brand"><span class="brand__square"></span><span>Thornbury Building Company</span></div>
  </section>
</main>
</body>
</html>
```